Business card (AI file uploaded)

We need a business card design that is minimalist using existing logo (attached). Source files must be editable so we can make the same design with other names.

Screenshots included of a design I was working on to give you an idea of the style I would like. Looking for similar modern styles

Thanks

```html
<!DOCTYPE html>
<html lang="en">
<head>
<meta charset="utf-8">
<title>Jordan Vale – Business Card</title>
<link rel="stylesheet" href="https://fonts.googleapis.com/css2?family=Open+Sans:wght@600;700;800&display=swap">
<style>
  :root {
    --ink: #1c1d1f;
    --ink-soft: #23282e;
    --paper-top: #ffffff;
    --paper-bottom: #c5cbcd;
    --band-top: #3fb5ea;
    --band-mid: #1f86d0;
    --band-bottom: #0d4e9e;
    --band-text: #13212e;
    --practice-text: #eef2f5;
    --mark: #141414;
  }
  * { margin: 0; padding: 0; box-sizing: border-box; }
  html, body {
    width: 1200px; height: 702px; overflow: hidden;
    background: #ffffff;
  }
  .card {
    position: relative;
    width: 1200px; height: 702px;
    overflow: hidden;
    font-family: "Open Sans", Arial, sans-serif;
    background: linear-gradient(to bottom, var(--paper-top) 0%, #eef0f0 35%, var(--paper-bottom) 100%);
  }
  .identity { position: absolute; left: 0; top: 0; }
  .identity__name {
    position: absolute; left: 147px; top: 92px;
    font-size: 58px; font-weight: 700; letter-spacing: 5px;
    color: var(--ink); white-space: nowrap;
  }
  .identity__title {
    position: absolute; left: 258px; top: 170px;
    font-size: 19px; font-weight: 700; letter-spacing: 1.5px;
    color: var(--ink); white-space: nowrap;
  }
  .identity__email {
    position: absolute; left: 166px; top: 204px;
    font-size: 26px; font-weight: 700; letter-spacing: 2.5px;
    color: var(--ink); white-space: nowrap;
  }
  .brand {
    position: absolute; left: 868px; top: 72px; width: 250px;
    display: flex; flex-direction: column; align-items: center; gap: 18px;
  }
  .brand__dot {
    width: 140px; height: 140px; border-radius: 50%;
    background: var(--mark);
  }
  .brand__name {
    font-size: 26px; font-weight: 700; letter-spacing: 3px;
    color: var(--ink); white-space: nowrap;
  }
  .contact-band {
    position: absolute; left: 0; top: 544px; width: 1200px; height: 158px;
    border-radius: 8px 8px 0 0;
    background: linear-gradient(to bottom, var(--band-top) 0%, var(--band-mid) 55%, var(--band-bottom) 100%);
    text-align: center;
  }
  .contact-band__address {
    position: absolute; left: 0; right: 0; top: 12px;
    font-size: 25px; font-weight: 700; letter-spacing: 2px;
    color: var(--band-text);
  }
  .contact-band__phones {
    position: absolute; left: 0; right: 0; top: 56px;
    font-size: 22px; font-weight: 700; letter-spacing: 2.5px;
    color: var(--band-text); word-spacing: 4px;
  }
  .contact-band__phones span + span { margin-left: 18px; }
  .contact-band__practice {
    position: absolute; left: 0; right: 0; top: 94px;
    font-size: 33px; font-weight: 700; letter-spacing: 3px;
    color: var(--practice-text);
    text-shadow: 1px 2px 2px rgba(0, 0, 0, 0.55);
  }
</style>
</head>
<body>
  <div class="card">
    <div class="identity">
      <div class="identity__name">JORDAN VALE</div>
      <div class="identity__title">ATTORNEY AT LAW</div>
      <div class="identity__email">vale@valelegal.com</div>
    </div>

    <div class="brand">
      <div class="brand__dot"></div>
      <div class="brand__name">VALE LEGAL</div>
    </div>

    <div class="contact-band">
      <div class="contact-band__address">410 Meridian Ave., Suite 300, Lakeview, IL 60500</div>
      <div class="contact-band__phones"><span>TEL. 555.014.2287</span><span>FAX. 555.014.2290</span></div>
      <div class="contact-band__practice">Real Estate | Bankruptcy | Social Security Disability</div>
    </div>
  </div>
</body>
</html>
```